Quill Petal Loft Hair Salon needs a Webpage design

Quill Petal Loft in Englewood is looking to start their web page, url and business emails, we want to be able to upload pictures and videos on the website. we do blow outs , makeup, color, lash extension, gel manicures

Target Market(s)

everyone

Industry/Entity Type

Beauty Salon

Coding

Coded - Design and coding required

Number of Pages Required

5+ page

Font styles to use
Serif

Colors
ffcf3e
9d9d9d
000000
ffffff

Requirements
Must have
• about us, contact us, products, menu, location, gallery, press
Nice to have
• play video gallery

```html
<!DOCTYPE html>
<html lang="en">
<head>
<meta charset="utf-8">
<title>Quill Petal Loft — Hair & Beauty Bar</title>
<link href="https://fonts.googleapis.com/css2?family=Open+Sans:ital,wght@0,400;0,600;0,700;1,400&family=Lora:ital,wght@1,600&display=swap" rel="stylesheet">
<style>
:root{
  --gold:#ffcf3e;
  --gold-deep:#e8b21f;
  --grey:#9d9d9d;
  --black:#000000;
  --white:#ffffff;
  --ink:#333333;
  --dark:#1b1b1b;
  --light:#efefef;
  --link:#d9a214;
}
*{box-sizing:border-box;margin:0;padding:0}
html,body{width:1200px;height:3508px;overflow:hidden}
body{font-family:"Open Sans",Arial,sans-serif;color:var(--ink);background:var(--white)}

/* Header + hero */
.hero{position:relative;height:688px;overflow:hidden}
.hero-photo{position:absolute;inset:0;background:radial-gradient(ellipse at 62% 40%,#e6b45a 0%,#b57a2c 30%,#5a3a14 65%,#2a1a08 100%)}
.hero-shade{position:absolute;inset:0;background:linear-gradient(180deg,rgba(0,0,0,.35) 0%,rgba(0,0,0,0) 30%,rgba(0,0,0,.15) 100%)}
.brand{position:absolute;left:0;top:0;width:230px;height:128px;background:var(--white);display:flex;align-items:center;justify-content:center;gap:12px}
.brand-dot{width:18px;height:18px;border-radius:50%;background:var(--gold)}
.brand-name{font-weight:700;font-size:24px;color:var(--gold-deep);line-height:1.1;width:150px}
.follow{position:absolute;top:26px;right:40px;display:flex;align-items:center;gap:10px;color:var(--white);font-size:15px}
.follow .soc{width:26px;height:26px;border-radius:50%;background:var(--white)}
.follow .phone{margin-left:26px;display:flex;align-items:center;gap:8px}
.nav{position:absolute;top:68px;right:40px;display:flex;background:rgba(0,0,0,.55);height:44px}
.nav a{color:var(--white);text-decoration:none;font-size:14px;font-weight:600;padding:0 22px;line-height:44px;text-transform:uppercase}
.nav a.on{background:var(--gold);color:var(--black)}
.hero-title{position:absolute;top:330px;left:0;right:0;text-align:center;color:var(--white);font-weight:700;font-size:56px;text-shadow:0 2px 8px rgba(0,0,0,.4)}
.hero-sub{position:absolute;top:428px;left:0;right:0;text-align:center;color:var(--gold);font-family:"Lora",Georgia,serif;font-style:italic;font-weight:600;font-size:34px}
.dots{position:absolute;top:632px;left:0;right:0;display:flex;justify-content:center;gap:10px}
.dots i{width:12px;height:12px;border-radius:50%;background:rgba(255,255,255,.6)}
.dots i.on{background:var(--white)}

/* What we do */
.services{height:584px;background:linear-gradient(180deg,#222 0%,#111 100%);position:relative;padding-top:56px}
.sec-title{text-align:center;font-size:40px;font-weight:400;letter-spacing:1px;line-height:1.2}
.services .sec-title{color:var(--white)}
.rule{width:90px;height:4px;background:var(--gold);margin:16px auto 0}
.arrows{position:absolute;right:72px;top:60px;display:flex;gap:6px}
.arrows span{width:34px;height:34px;background:#3a3a3a;display:flex;align-items:center;justify-content:center}
.service-list{display:flex;justify-content:space-around;padding:56px 60px 0}
.service{text-align:center;width:250px}
.service .pic{width:236px;height:236px;border-radius:50%;margin:0 auto;border:6px solid var(--white)}
.service .name{color:#cfcfcf;font-size:30px;margin-top:16px}

/* Welcome */
.welcome{height:348px;padding:44px 72px 0;background:var(--white)}
.welcome .sec-title{color:#444;font-size:50px}
.welcome .text{margin-top:30px}
.welcome p{font-size:13.5px;line-height:1.6;color:#666;margin-bottom:16px;text-align:center}

/* Gallery */
.gallery{height:740px;background:var(--light);padding-top:54px}
.gallery .sec-title{color:var(--ink);font-size:46px}
.grid{display:grid;grid-template-columns:repeat(3,344px);grid-auto-rows:270px;gap:8px;justify-content:center;margin-top:40px}

/* Press */
.press{height:600px;position:relative;background:var(--white)}
.press h2{position:absolute;left:72px;top:36px;font-size:40px;font-weight:400;color:var(--ink)}
.press h2::after{content:"";display:block;width:70px;height:4px;background:var(--gold);margin-top:8px}
.articles{position:absolute;left:72px;top:128px;width:720px}
.article{border-bottom:1px solid #e2e2e2;padding:14px 0}
.article h3{color:var(--link);font-size:16px;font-weight:600}
.article .meta{font-size:12px;color:var(--grey);margin:4px 0}
.article p{font-size:13px;color:#666;line-height:1.5}
.more{position:absolute;left:72px;top:520px;font-size:14px;color:#444}
.feed{position:absolute;left:820px;top:36px;width:308px;height:380px;border:1px solid #cfcfcf;background:var(--white)}
.feed-head{background:#f1f1f1;font-size:13px;padding:8px 12px;color:#555;border-bottom:1px solid #ddd}
.feed-page{display:flex;gap:10px;padding:12px}
.feed-page .thumb{width:60px;height:60px;background:var(--gold)}
.feed-page b{font-size:14px;color:#3b4f8a}
.feed-page small{display:block;font-size:11px;color:var(--grey)}
.feed-post{margin:0 12px;font-size:11px;color:#666;line-height:1.5;border-top:1px solid #eee;padding-top:8px;height:170px}
.feed-faces{display:flex;gap:6px;padding:8px 12px;flex-wrap:wrap}
.feed-faces span{width:40px;height:40px;background:#cfcfcf}

/* Map */
.map{height:220px;background:linear-gradient(135deg,#e9e5dc 0%,#ddd8cc 50%,#e6e1d6 100%)}

/* Footer */
.footer{height:300px;background:var(--gold);padding:32px 72px 0;display:grid;grid-template-columns:290px 260px 290px 240px}
.footer h4{font-size:16px;font-weight:700;color:var(--black);text-transform:uppercase;margin-bottom:16px}
.footer li{list-style:none;font-size:13px;color:#3a2d00;margin-bottom:10px;display:flex;align-items:center;gap:10px}
.footer .mini{width:10px;height:10px;background:#3a2d00;border-radius:50%;flex:none}
.hours li{justify-content:space-between;width:240px}
.socials{display:flex;gap:8px;margin-top:6px}
.socials span{width:26px;height:26px;border-radius:50%;background:var(--black)}
.insta{display:grid;grid-template-columns:repeat(2,90px);gap:8px}
.insta span{height:70px;background:#8a6a2a}
.copyright{height:28px;background:var(--dark);color:var(--grey);font-size:12px;text-align:center;line-height:28px}
</style>
</head>
<body>

<header class="hero">
  <div class="hero-photo" role="img" aria-label="Photo of a woman with glossy golden blonde curls"></div>
  <div class="hero-shade"></div>
  <div class="brand"><span class="brand-dot"></span><span class="brand-name">Quill Petal Loft</span></div>
  <div class="follow">Follow us on
    <span class="soc"></span><span class="soc"></span><span class="soc"></span><span class="soc"></span>
    <span class="phone">
      <svg width="16" height="16" viewBox="0 0 24 24"><path fill="#fff" d="M6.6 10.8a15 15 0 006.6 6.6l2.2-2.2c.3-.3.7-.4 1-.2 1.1.4 2.3.6 3.6.6.6 0 1 .4 1 1V20c0 .6-.4 1-1 1A17 17 0 013 4c0-.6.4-1 1-1h3.5c.6 0 1 .4 1 1 0 1.3.2 2.5.6 3.6.1.3 0 .7-.2 1z"/></svg>
      +123-456-7890</span>
  </div>
  <nav class="nav">
    <a class="on">Home</a><a>About Us</a><a>Press</a><a>Gallery</a><a>Products</a><a>Contact Us</a>
  </nav>
  <h1 class="hero-title">Quill Petal Loft Englewood</h1>
  <p class="hero-sub">Full service Hair and Beauty Bar</p>
  <div class="dots"><i class="on"></i><i></i><i></i><i></i></div>
</header>

<section class="services">
  <h2 class="sec-title">WHAT WE DO</h2>
  <div class="rule"></div>
  <div class="arrows">
    <span><svg width="12" height="12" viewBox="0 0 12 12"><path d="M8 1L3 6l5 5" stroke="#fff" stroke-width="2" fill="none"/></svg></span>
    <span><svg width="12" height="12" viewBox="0 0 12 12"><path d="M4 1l5 5-5 5" stroke="#fff" stroke-width="2" fill="none"/></svg></span>
  </div>
  <div class="service-list">
    <div class="service"><div class="pic" role="img" aria-label="Blow out styling photo" style="background:radial-gradient(circle,#d6b58a,#7a5534)"></div><div class="name">Blow Outs</div></div>
    <div class="service"><div class="pic" role="img" aria-label="Vivid red hair color photo" style="background:radial-gradient(circle,#c9542a,#5a1a10)"></div><div class="name">Color</div></div>
    <div class="service"><div class="pic" role="img" aria-label="Haircut in progress photo" style="background:radial-gradient(circle,#c9a75a,#4a3a20)"></div><div class="name">Cuts</div></div>
    <div class="service"><div class="pic" role="img" aria-label="Smooth keratin treated hair photo" style="background:radial-gradient(circle,#e8c98a,#9a7040)"></div><div class="name">keratin</div></div>
  </div>
</section>

<section class="welcome">
  <h2 class="sec-title">Welcome to Quill Petal Loft</h2>
  <div class="text">
    <p>Quill Petal Loft is a neighborhood hair and beauty bar built for easy, polished days. Our stylists offer blow outs, color, cuts, keratin smoothing, makeup, lash extensions and gel manicures in a bright, relaxed space. Every visit starts with a short consultation so we can shape a look that suits your hair, your schedule and the way you like to feel when you walk out the door.</p>
    <p>We opened our doors in Englewood with a simple idea: great service should feel personal. Book a quick blow out before an event, plan a full color refresh, or settle in for a lash and nail afternoon with friends. Our team keeps learning new techniques each season and uses gentle, salon quality products that care for hair and skin alike.</p>
  </div>
</section>

<section class="gallery">
  <h2 class="sec-title">OUR GALLERY</h2>
  <div class="rule"></div>
  <div class="grid">
    <div role="img" aria-label="Woman with auburn waves" style="background:linear-gradient(135deg,#c07a4a,#5a2a14)"></div>
    <div role="img" aria-label="Bold makeup look with blue eyeshadow" style="background:linear-gradient(135deg,#e6b9a2,#3a6a9a)"></div>
    <div role="img" aria-label="Hands applying lotion" style="background:linear-gradient(135deg,#f3ddd0,#d6a58c)"></div>
    <div role="img" aria-label="Woman with long sleek black hair" style="background:linear-gradient(135deg,#8a8a8a,#151515)"></div>
    <div role="img" aria-label="Facial mask treatment" style="background:linear-gradient(135deg,#f4ece6,#c8b2a4)"></div>
    <div role="img" aria-label="Red gel manicure" style="background:linear-gradient(135deg,#f2e0da,#c21f3a)"></div>
  </div>
</section>

<section class="press">
  <h2>Press</h2>
  <div class="articles">
    <div class="article"><h3>Varden Could Be Shopping Some Assets To Help Reduce Debt</h3><div class="meta">Staff writer, Aug 20 in Business News</div><p>Local salons see steady growth as clients return for regular color, cuts and blow outs. Owners say loyal guests and friendly service keep chairs full through every season.</p></div>
    <div class="article"><h3>Varden Could Be Shopping Some Assets To Help Reduce Debt</h3><div class="meta">Staff writer, Aug 20 in Business News</div><p>Local salons see steady growth as clients return for regular color, cuts and blow outs. Owners say loyal guests and friendly service keep chairs full through every season.</p></div>
    <div class="article"><h3>Varden Could Be Shopping Some Assets To Help Reduce Debt</h3><div class="meta">Staff writer, Aug 20 in Business News</div><p>Local salons see steady growth as clients return for regular color, cuts and blow outs. Owners say loyal guests and friendly service keep chairs full through every season.</p></div>
  </div>
  <div class="more">Read More ›</div>
  <aside class="feed">
    <div class="feed-head">Find us online</div>
    <div class="feed-page"><div class="thumb"></div><div><b>Quill Petal Loft</b><small>1,024 likes</small></div></div>
    <div class="feed-post">Quill Petal Loft: The beauty of a fresh blow out is how it lifts your whole week. Book your next visit today and bring a friend along.<br><br>Quill Petal Loft: New gel colors just arrived for fall. Stop by and pick a favorite shade.</div>
    <div class="feed-faces"><span></span><span></span><span></span><span></span><span></span><span></span></div>
  </aside>
</section>

<div class="map" role="img" aria-label="Map showing the salon location in Englewood"></div>

<footer class="footer">
  <div>
    <h4>Contact Us</h4>
    <ul>
      <li><span class="mini"></span>218 Linden Row, Englewood, CO</li>
      <li><span class="mini"></span>+123-456-7890</li>
      <li><span class="mini"></span>hello@quillpetalloft.example</li>
    </ul>
    <div class="socials"><span></span><span></span><span></span><span></span><span></span></div>
  </div>
  <div>
    <h4>Our Services</h4>
    <ul>
      <li><span class="mini"></span>Blow Outs</li>
      <li><span class="mini"></span>Lash Extensions</li>
      <li><span class="mini"></span>Gel Manicures</li>
      <li><span class="mini"></span>Makeup</li>
    </ul>
  </div>
  <div>
    <h4>Office Hours</h4>
    <ul class="hours">
      <li>Monday <span>9am to 7pm</span></li>
      <li>Tuesday <span>9am to 7pm</span></li>
      <li>Wednesday <span>9am to 7pm</span></li>
      <li>Thursday <span>9am to 7pm</span></li>
      <li>Friday <span>9am to 7pm</span></li>
    </ul>
  </div>
  <div>
    <h4>Instagram</h4>
    <div class="insta">
      <span role="img" aria-label="Salon photo"></span><span role="img" aria-label="Salon photo"></span>
      <span role="img" aria-label="Salon photo"></span><span role="img" aria-label="Salon photo"></span>
    </div>
  </div>
</footer>
<div class="copyright">Copyright 2016 - Quill Petal Loft - All Rights Reserved</div>

</body>
</html>
```